We need a card and logo design for a new business based in Dallas Texas called Stonemarsh Financial LLC.

We provide bridge loans.We offer pay day loans,title loans and check cashing.Our products are emmergency loans that help borrowers meet short term liquidity needs until the next pay check.

The final design should communicate,professionalism,Sophistication and friendliness to our customers.Use the color Blue as much as possible and another eye catching color if possible.We will consider a profesional looking knight logo with the color Blue in it.Please design a full corporate identity.

```html
<!DOCTYPE html>
<html lang="en">
<head>
<meta charset="utf-8">
<title>Stonemarsh Financial LLC – Business Card</title>
<link href="https://fonts.googleapis.com/css2?family=Cinzel:wght@600&family=Open+Sans:wght@400;600&display=swap" rel="stylesheet">
<style>
  :root {
    --backdrop: #38322e;
    --card-light: #f0f1f3;
    --navy: #233a7c;
    --ink: #111111;
    --rule: #8a8a8a;
    --blue-deep: #1d3f86;
    --blue-glow: #0a55b0;
    --white: #ffffff;
  }
  html, body {
    margin: 0;
    padding: 0;
    width: 1000px;
    height: 1200px;
    overflow: hidden;
    background: var(--backdrop);
  }
  .canvas {
    position: relative;
    width: 1000px;
    height: 1200px;
  }
  .card {
    position: absolute;
    width: 723px;
    height: 424px;
    box-sizing: border-box;
  }
  /* Front side */
  .card-front {
    left: 140px;
    top: 118px;
    background: var(--card-light);
  }
  .brand {
    position: absolute;
    left: 40px;
    top: 66px;
    display: flex;
    align-items: center;
    gap: 18px;
  }
  .brand-mark {
    width: 74px;
    height: 74px;
    border-radius: 50%;
    background: var(--navy);
  }
  .brand-name {
    font-family: "Cinzel", serif;
    font-weight: 600;
    color: var(--navy);
    line-height: 1;
    text-align: center;
  }
  .brand-name .line-main { display: block; font-size: 38px; letter-spacing: 1px; }
  .brand-name .line-sub { display: block; font-size: 23px; margin-top: 6px; letter-spacing: 1px; }
  .person {
    position: absolute;
    left: 51px;
    top: 226px;
  }
  .person-name {
    font-family: "Cinzel", serif;
    font-weight: 600;
    font-size: 26px;
    color: var(--navy);
    margin: 0;
    line-height: 1;
  }
  .person-title {
    font-family: "Open Sans", sans-serif;
    font-weight: 600;
    font-size: 18px;
    color: var(--ink);
    margin: 4px 0 0;
  }
  .contact {
    position: absolute;
    top: 300px;
    font-family: "Open Sans", sans-serif;
    font-size: 16px;
    color: var(--ink);
    margin: 0;
    display: grid;
    row-gap: 8px;
    line-height: 1.4;
  }
  .contact dt { color: var(--navy); font-weight: 600; grid-column: 1; }
  .contact dd { margin: 0; grid-column: 2; }
  .contact-left { left: 51px; grid-template-columns: 62px auto; }
  .contact-right { left: 379px; grid-template-columns: 76px auto; }
  .contact-divider {
    position: absolute;
    left: 361px;
    top: 294px;
    width: 1px;
    height: 81px;
    background: var(--rule);
  }
  /* Back side */
  .card-back {
    left: 125px;
    top: 637px;
    background: radial-gradient(ellipse at 50% 40%, var(--blue-glow) 0%, var(--blue-deep) 70%);
    display: flex;
    flex-direction: column;
    align-items: center;
  }
  .card-back .brand-mark {
    margin-top: 110px;
    width: 120px;
    height: 120px;
    background: var(--white);
  }
  .card-back .brand-name {
    color: var(--white);
    margin-top: 44px;
  }
  .card-back .brand-name .line-main { font-size: 46px; letter-spacing: 2px; }
  .card-back .brand-name .line-sub { font-size: 27px; margin-top: 8px; }
</style>
</head>
<body>
<main class="canvas">
  <section class="card card-front" aria-label="Card front">
    <div class="brand">
      <span class="brand-mark" aria-hidden="true"></span>
      <p class="brand-name" style="margin:0">
        <span class="line-main">STONEMARSH</span>
        <span class="line-sub">FINANCIAL LLC.</span>
      </p>
    </div>
    <div class="person">
      <h1 class="person-name">DANIEL HARTLEY</h1>
      <p class="person-title">Financial Advisor</p>
    </div>
    <dl class="contact contact-left">
      <dt>Phone:</dt><dd>111-123-4567</dd>
      <dt>Email:</dt><dd>info@stonemarshfinancial.com</dd>
    </dl>
    <span class="contact-divider" aria-hidden="true"></span>
    <dl class="contact contact-right">
      <dt>Fax:</dt><dd>111-123-4567</dd>
      <dt>Address:</dt><dd>XXX Some Street Address<br>State, Country</dd>
    </dl>
  </section>

  <section class="card card-back" aria-label="Card back">
    <span class="brand-mark" aria-hidden="true"></span>
    <p class="brand-name" style="margin-bottom:0">
      <span class="line-main">STONEMARSH</span>
      <span class="line-sub">FINANCIAL LLC.</span>
    </p>
  </section>
</main>
</body>
</html>
```